Kestrel Facilities Business Card Design

We would now like to design business cards with the new Kestrel Facilities logo

Target Market(s)

Professional

Industry/Entity Type

Professional services

Contact Information for Business Card

Employee name, title, phone number, email address, corporate office address and logo.

Font styles to use
Sans Serif

Colors
0054AA
0677BA
7BADD7
CADEEF
E8F1F8

Requirements
Must have
• My logo
Should not have
• any other pictures or images besides my logo

```html
<!DOCTYPE html>
<html lang="en">
<head>
<meta charset="utf-8">
<title>Kestrel Facilities Business Card</title>
<link rel="stylesheet" href="https://fonts.googleapis.com/css2?family=Montserrat:wght@400;500;700&display=swap">
<style>
  :root {
    --brand-blue: #3176bc;
    --brand-deep: #0054aa;
    --paper: #ffffff;
    --ink: #1c1c1c;
    --pale: #e8f1f8;
    --stage: #2b2b2b;
    --logo-light: #cadeef;
  }
  * { margin: 0; padding: 0; box-sizing: border-box; }
  html, body {
    width: 1200px; height: 960px; overflow: hidden;
    background: var(--stage);
    font-family: "Montserrat", sans-serif;
  }
  .canvas { position: relative; width: 1200px; height: 960px; }
  .card {
    position: absolute; width: 560px; height: 320px;
    border-radius: 22px; overflow: hidden;
  }
  .card-front { left: 60px; top: 90px; background: var(--brand-blue); }
  .card-back { left: 580px; top: 530px; background: var(--paper); }

  .brand {
    position: absolute; display: flex; align-items: center; gap: 12px;
    font-weight: 700; letter-spacing: 0.04em; text-transform: uppercase;
  }
  .brand-mark { width: 34px; height: 34px; border: 6px solid currentColor; }
  .card-front .brand {
    left: 50%; top: 50%; transform: translate(-50%, -50%);
    color: var(--logo-light); font-size: 34px;
  }
  .card-back .brand {
    left: 200px; top: 58px; color: var(--brand-blue); font-size: 26px;
  }
  .card-back .brand-mark { width: 28px; height: 28px; border-width: 5px; }

  .back-shape { position: absolute; inset: 0; }

  .person { position: absolute; right: 300px; top: 178px; text-align: right; }
  .person-name { color: var(--brand-blue); font-weight: 700; font-size: 22px; letter-spacing: 0.01em; }
  .person-title { color: var(--ink); font-size: 15px; margin-top: 4px; }

  .divider { position: absolute; left: 278px; top: 160px; width: 2px; height: 78px; background: var(--brand-blue); }

  .contact-list { position: absolute; left: 296px; top: 160px; list-style: none; }
  .contact-list li {
    display: flex; align-items: center; gap: 8px;
    font-size: 14px; color: var(--ink); line-height: 25px;
  }
  .contact-list svg { width: 14px; height: 14px; fill: var(--brand-blue); flex: none; }

  .address {
    position: absolute; left: 0; right: 0; top: 256px; text-align: center;
    font-size: 14.5px; color: var(--ink);
  }
</style>
</head>
<body>
<main class="canvas">

  <section class="card card-front" aria-label="Card front">
    <div class="brand"><span class="brand-mark"></span>Kestrel Facilities</div>
  </section>

  <section class="card card-back" aria-label="Card back">
    <svg class="back-shape" viewBox="0 0 560 320" preserveAspectRatio="none" aria-hidden="true">
      <rect width="560" height="320" fill="var(--brand-blue)"/>
      <path d="M0 70 C 160 30, 380 10, 560 70 L560 250 C 420 300, 250 320, 90 300 C 50 290, 20 260, 0 230 Z" fill="var(--paper)"/>
    </svg>

    <div class="brand"><span class="brand-mark"></span>Kestrel Facilities</div>

    <div class="person">
      <p class="person-name">DANA WHITCOMBE</p>
      <p class="person-title">Co-Founder</p>
    </div>

    <div class="divider"></div>

    <ul class="contact-list">
      <li>
        <svg viewBox="0 0 24 24"><path d="M6.6 10.8a15.1 15.1 0 0 0 6.6 6.6l2.2-2.2c.3-.3.7-.4 1-.2 1.1.4 2.3.6 3.6.6.6 0 1 .4 1 1V20c0 .6-.4 1-1 1A17 17 0 0 1 3 4c0-.6.4-1 1-1h3.5c.6 0 1 .4 1 1 0 1.3.2 2.5.6 3.6.1.3 0 .7-.2 1z"/></svg>
        +254-700-41235
      </li>
      <li>
        <svg viewBox="0 0 24 24"><path d="M2 5h20v14H2z M2 5l10 8 10-8" fill="none" stroke="var(--brand-blue)" stroke-width="2.4"/></svg>
        hello@kestrelfm.com
      </li>
      <li>
        <svg viewBox="0 0 24 24"><circle cx="12" cy="12" r="10"/></svg>
        www.kestrelfm.com
      </li>
    </ul>

    <p class="address">418 N. Harbor Lane Suite 220 Lakeview 14</p>
  </section>

</main>
</body>
</html>
```